MRT Property - Business Cards

Looking for a business card & general letterhead, signage etc design for our new logo.

Colours:
000a20
0056a2
00b5ef
0088ce
68cef2

Fonts:
Poppins
Karla

Please keep look and feel of new brand - example in the zip package I sent.

```html
<!DOCTYPE html>
<html lang="en">
<head>
<meta charset="utf-8">
<title>MRT Property – Business Cards</title>
<link rel="stylesheet" href="https://fonts.googleapis.com/css2?family=Poppins:wght@400;500;600;700&display=swap">
<style>
  :root {
    --navy: #000a20;
    --card: #10162a;
    --blue-deep: #0056a2;
    --blue-mid: #0088ce;
    --blue-bright: #00b5ef;
    --blue-light: #68cef2;
    --white: #ffffff;
    --stage: #e8ebf0;
  }
  * { box-sizing: border-box; margin: 0; padding: 0; }
  html, body { width: 1200px; height: 780px; overflow: hidden; }
  body {
    background: var(--stage);
    font-family: "Poppins", sans-serif;
    display: flex;
    align-items: center;
    justify-content: center;
    gap: 40px;
  }
  .card {
    position: relative;
    width: 520px;
    height: 300px;
    background: var(--card);
    border-radius: 4px;
    box-shadow: 0 10px 26px rgba(0, 10, 32, 0.28);
    overflow: hidden;
  }

  /* Front */
  .brand-name {
    position: absolute;
    left: 44px;
    top: 86px;
    font-weight: 600;
    font-size: 30px;
    line-height: 1.1;
    color: var(--blue-deep);
    letter-spacing: 0.5px;
  }
  .divider {
    position: absolute;
    left: 240px;
    top: 48px;
    width: 40px;
    height: 170px;
  }
  .contact-block {
    position: absolute;
    left: 290px;
    top: 72px;
    color: var(--white);
  }
  .person-name {
    font-weight: 600;
    font-size: 27px;
    line-height: 1.1;
    color: var(--blue-deep);
  }
  .person-name .surname { font-weight: 400; color: var(--blue-light); }
  .person-role {
    font-weight: 500;
    font-size: 13px;
    margin-top: 2px;
  }
  .contact-list {
    list-style: none;
    margin-top: 14px;
    font-size: 12px;
    line-height: 1.75;
  }
  .contact-list li { display: flex; align-items: center; gap: 8px; }
  .contact-list svg { width: 12px; height: 12px; flex: none; }
  .address {
    position: absolute;
    left: 44px;
    right: 30px;
    bottom: 28px;
    font-size: 12.5px;
    color: var(--white);
    letter-spacing: 0.2px;
  }

  /* Back */
  .card-back .brand-name {
    left: auto;
    top: auto;
    right: 40px;
    bottom: 36px;
  }
</style>
</head>
<body>

  <section class="card card-front" aria-label="Business card front">
    <div class="brand-name">MRT Property</div>

    <svg class="divider" viewBox="0 0 40 170" aria-hidden="true">
      <defs>
        <linearGradient id="divider-fade" x1="0" y1="0" x2="0" y2="1">
          <stop offset="0" stop-color="#0088ce" stop-opacity="0.2"/>
          <stop offset="0.5" stop-color="#0088ce"/>
          <stop offset="1" stop-color="#0088ce" stop-opacity="0.2"/>
        </linearGradient>
      </defs>
      <line x1="34" y1="0" x2="6" y2="170" stroke="url(#divider-fade)" stroke-width="1.2"/>
    </svg>

    <div class="contact-block">
      <h1 class="person-name">Callum <span class="surname">Reeve</span></h1>
      <p class="person-role">Director</p>
      <ul class="contact-list">
        <li>
          <svg viewBox="0 0 24 24" aria-hidden="true"><path fill="#68cef2" d="M6.6 10.8a15.1 15.1 0 0 0 6.6 6.6l2.2-2.2a1 1 0 0 1 1-.25 11.4 11.4 0 0 0 3.6.57 1 1 0 0 1 1 1V20a1 1 0 0 1-1 1A17 17 0 0 1 3 4a1 1 0 0 1 1-1h3.5a1 1 0 0 1 1 1c0 1.25.2 2.45.57 3.57a1 1 0 0 1-.25 1z"/></svg>
          +61 2 9000 4182
        </li>
        <li>
          <svg viewBox="0 0 24 24" aria-hidden="true"><circle cx="12" cy="12" r="9.5" fill="none" stroke="#68cef2" stroke-width="2"/><path d="M2.5 12h19M12 2.5c3 3 3 16 0 19M12 2.5c-3 3-3 16 0 19" fill="none" stroke="#68cef2" stroke-width="1.6"/></svg>
          www.mrtproperty.com.au
        </li>
        <li>
          <svg viewBox="0 0 24 24" aria-hidden="true"><rect x="2" y="5" width="20" height="14" rx="2" fill="none" stroke="#68cef2" stroke-width="2"/><path d="M3 6l9 7 9-7" fill="none" stroke="#68cef2" stroke-width="2"/></svg>
          info@mrtproperty.com.au
        </li>
      </ul>
    </div>

    <p class="address">Suite 114, Level 3 18 Harbourview Road Rhodes NSW 2138</p>
  </section>

  <section class="card card-back" aria-label="Business card back">
    <div class="brand-name">MRT Property</div>
  </section>

</body>
</html>
```